Local Newspaper Quarterly " Meet The Realtor" print ad

I need a new add made up. This was my last ad:
http://www.harborpostlistings.example/static/pdfs/agents1309/Ar092213%20G10%20006%20Prepress.pdf

I do not really care of Realtor advertisements because they are just so cheesy and rather pompous-like. However, it's a necessary evil
My ads have always been outside of the box and/or visually sharp.
I now have a new company' Voss Real Estate( I will attach a logo) contact info:
Colm Voss
Voss Real Estate
Broker/Owner( this can be somewhere in small print or corner of ad since it's mandatory to have shown
Phone: 304-555-0147
Email: Colm@VossRealEstate.Example
VossRealEstate.Example
I would like social icons(FB,Twitter, Pinterest! Houzz, Gplus)

Ideas: In my logo font or using the image at the top I envision
Something like:
A
Voss Real Estate
Of Mind
Body of ad?
Images of Charleston WV as a real light back ground
With 3 or 4 customer reviews chosen by you in this site:
http://webcolm.example/think.html

Bottom: contact info and my name in a nice Signature style ??
My agent pic at the bottom right( to be small. I don't want my big head overshadowing the message)

I have yet to think of a tagline for my new company:
I have been thinking of " Luxury Services For All Things Real Estate"

Or nothing at all ??? I don't care for tag lines but then again that's part of the business

Target Market(s)

Higher end homes

Industry/Entity Type

Business

Colors
0f59a5
0392cd
0f0f0f
eaeaea
ffffff

Requirements
Must have
• My logo and colors
Nice to have
• My agent picture and client review.
Should not have
• No typical real estate images like a house or home buyer

```html
<!DOCTYPE html>
<html lang="en">
<head>
<meta charset="utf-8">
<title>Voss Real Estate – Meet The Realtor</title>
<link rel="stylesheet" href="https://fonts.googleapis.com/css2?family=Jost:wght@300;400;500;700&display=swap">
<style>
  :root {
    --brand-blue: #0f6db5;
    --brand-deep: #0f59a5;
    --brand-sky: #0392cd;
    --ink: #0f0f0f;
    --band-dark: #3b3b3b;
    --icon-ink: #3b3b3b;
    --mist: #eaeaea;
    --white: #ffffff;
    --muted: #d0d0d0;
  }
  * { margin: 0; padding: 0; box-sizing: border-box; }
  html, body { width: 774px; height: 1200px; overflow: hidden; background: var(--white); }
  body { font-family: "Jost", "Futura", sans-serif; color: var(--white); }
  .ad { position: relative; width: 774px; height: 1200px; background: var(--white); overflow: hidden; }

  .brand-mark {
    position: absolute; left: 323px; top: 30px; width: 127px; height: 127px;
    background: linear-gradient(135deg, #8e8e8e, #5f5f5f 55%, #7a7a7a);
    display: flex; align-items: center; justify-content: center; text-align: center;
  }
  .brand-mark span {
    font-weight: 500; font-size: 17px; line-height: 1.15; color: var(--white);
    letter-spacing: 0.04em; text-transform: uppercase;
  }

  .city-view {
    position: absolute; left: 0; top: 178px; width: 774px; height: 434px;
    background: linear-gradient(180deg,
      #b9c6d6 0%, #eef1f4 12%, #dfe4ea 20%, #b4bcc4 25%,
      #7b7560 28%, #6d6a5a 31%,
      #8c6a55 34%, #a56a52 40%, #c9b9a8 46%, #8e6d58 52%,
      #6f8a52 55%, #8a8a6a 58%,
      #5c7a5e 62%, #6b8a6c 72%, #5e7c5f 84%,
      #a86a52 88%, #b5705a 94%, #7a5e4c 100%);
  }

  .blue-field { position: absolute; left: 0; top: 611px; width: 774px; height: 589px; background: var(--brand-blue); }

  .tagline-top {
    position: absolute; left: 33px; top: 549px; font-weight: 300; font-size: 84px;
    line-height: 1; letter-spacing: -0.5px; text-shadow: 0 2px 4px rgba(0,0,0,0.35);
  }
  .tagline-small {
    position: absolute; left: 130px; top: 660px; font-weight: 300; font-size: 38px;
    line-height: 1.15; text-align: right; width: 115px;
  }
  .tagline-big {
    position: absolute; left: 256px; top: 645px; font-weight: 400; font-size: 108px;
    line-height: 1; letter-spacing: -1px; text-shadow: 0 2px 4px rgba(0,0,0,0.3);
  }

  .reviews { position: absolute; left: 263px; top: 781px; width: 476px; font-weight: 300; font-size: 12.2px; line-height: 15.6px; text-align: justify; }
  .reviews p { margin-bottom: 15.6px; }
  .reviews .reviewer { font-style: italic; font-weight: 400; }
  .reviews .cta { font-weight: 400; }

  .contact-band { position: absolute; left: 0; top: 1062px; width: 774px; height: 100px; background: var(--band-dark); }
  .agent-photo {
    position: absolute; left: 37px; top: 1065px; width: 108px; height: 108px;
    border: 2px solid var(--white);
    background: linear-gradient(180deg, #b8862e 0%, #8f5d22 45%, #c7cdd6 100%);
  }
  .contact { position: absolute; left: 159px; top: 1089px; }
  .contact .name { font-weight: 700; font-size: 13.5px; letter-spacing: 0.06em; color: var(--white); }
  .contact .detail { font-weight: 300; font-size: 10.5px; line-height: 15px; color: var(--muted); letter-spacing: 0.02em; }
  .contact .name + .detail { margin-top: 2px; }

  .social { position: absolute; left: 530px; top: 1112px; display: flex; gap: 10.4px; }
  .social svg { width: 26px; height: 26px; display: block; }
  .social rect { fill: var(--white); }
  .social .glyph { fill: none; stroke: var(--icon-ink); stroke-width: 2; stroke-linecap: round; stroke-linejoin: round; }
  .social .solid { fill: var(--icon-ink); stroke: none; }
</style>
</head>
<body>
<main class="ad">
  <div class="brand-mark"><span>Voss<br>Real Estate</span></div>

  <div class="city-view" role="img" aria-label="Elevated view of a riverside downtown skyline with a steel truss bridge, green river and hills under a cloudy sky"></div>

  <div class="blue-field"></div>

  <h1>
    <span class="tagline-top">Luxury Services</span>
    <span class="tagline-small">For All<br>Things</span>
    <span class="tagline-big">Real Estate</span>
  </h1>

  <section class="reviews">
    <p>See what the people are saying...</p>
    <p>In trying to buy a home from long distance, Colm went above and beyond his duty as my Realtor. His professionalism, knowledge and attentiveness were absolutely superb! What could have been a nightmare experience, turned out to be a wonderfully smooth transition. Thanks for all your help – it was truly appreciated! A++ <span class="reviewer">~ Dana Whitlock</span></p>
    <p>In this difficult sales market, I believe every effort was made to sell our home successfully. We truly appreciate the expenditure of time , energy and resources by Keystone Realty Group and their encouragement and persistence extended in this successful outcome. <span class="reviewer">~ Owen and Clara Hestler</span></p>
    <p>We have and will recommend Colm Voss to anyone looking to buy or sell any Real Estate. We feel Colm did an exceptional job selling our property even that it was was at the low end of the Real Estate market. <span class="reviewer">~ Marcus and Jill Ardent</span></p>
    <p class="cta">Call me today to book an appointment.</p>
  </section>

  <footer>
    <div class="contact-band"></div>
    <div class="agent-photo" role="img" aria-label="Portrait photo of the agent outdoors with autumn foliage behind"></div>
    <div class="contact">
      <div class="name">Colm Voss - For more information call 304-555-0147</div>
      <div class="detail">Broker/Owner • Voss Real Estate</div>
      <div class="detail">Colm@VossRealEstate.Example</div>
      <div class="detail">Visit VossRealEstate.Example today.</div>
    </div>
    <div class="social" aria-label="Social media links">
      <svg viewBox="0 0 26 26" aria-label="Share"><rect width="26" height="26"/><circle class="solid" cx="8" cy="13" r="2.6"/><circle class="solid" cx="18" cy="7.5" r="2.6"/><circle class="solid" cx="18" cy="18.5" r="2.6"/><path class="glyph" d="M8 13 L18 7.5 M8 13 L18 18.5"/></svg>
      <svg viewBox="0 0 26 26" aria-label="Chat"><rect width="26" height="26"/><path class="glyph" d="M6 7 H20 V16 H12 L8 20 V16 H6 Z"/></svg>
      <svg viewBox="0 0 26 26" aria-label="Link"><rect width="26" height="26"/><path class="glyph" d="M11 15 L15 11 M10 12 L8 14 A3 3 0 0 0 12 18 L14 16 M16 14 L18 12 A3 3 0 0 0 14 8 L12 10"/></svg>
      <svg viewBox="0 0 26 26" aria-label="Favourites"><rect width="26" height="26"/><path class="solid" d="M13 20 L6.5 13.5 A3.6 3.6 0 0 1 13 8.8 A3.6 3.6 0 0 1 19.5 13.5 Z"/></svg>
      <svg viewBox="0 0 26 26" aria-label="Email"><rect width="26" height="26"/><path class="glyph" d="M6 8 H20 V18 H6 Z M6 8 L13 14 L20 8"/></svg>
      <svg viewBox="0 0 26 26" aria-label="Website"><rect width="26" height="26"/><circle class="glyph" cx="13" cy="13" r="7"/><path class="glyph" d="M6 13 H20 M13 6 C9.5 10 9.5 16 13 20 C16.5 16 16.5 10 13 6"/></svg>
    </div>
  </footer>
</main>
</body>
</html>
```